Private practice for psychiatry and psychotherapy needs a business card and logo

I need a logo and business card design for my private practice for psychiatry and psychotherapy. The optional names for my practice are: Vorsteling Praktijk voor Psychiatrie en Psychotherapie, or short: Praktijk Vorsteling.
I am a (child and adolescent) psychiatrist and psychotherapist. I diagnose and treat infants, children, adolescents and adults with psychiatric symptoms/disorders. I also give supervision to colleagues about their own treatments. My work is characterised by personal involvement, transparence, creativity and professionality.
I would like to have an appealing, light and bright, yet basic design that invites people (both children and adults) to contact me, gives trust and hope, without loosing professional appearance.
I uploaded my contact information which should not necessarily be all included (in this form) on the card as long as people know how to contact me. Please feel free to be creative!
Please note that my website is only temporarely and need a new design and update too!

Target Market(s)

Clients and patients (children, adolescents, adults) with psychiatric symptoms who need diagnosis and treatment. I work with private clients and patients through medical insurances.

Industry/Entity Type

Mental Health

Contact Information for Business Card

Dr. Ilse Vorsteling-ter Haaf
Psychiater/Kinder- en Jeugdpsychiater
Jorisvan Heultstraat 14
3071 PW Rotterdam
t: 06-58190274
e: info@praktijkvorsteling.nl
i: www.praktijkvorsteling.nl

Logo Text

Praktijk Vorsteling voor Psychiatrie en Psychotherapie; or short: Praktijk Vorsteling

Font styles to use
Sans Serif
Other font styles liked:
• up to designer

Requirements
Must have
• Appealing, light, bright, creative, trustful, professional and unique.

```html
<!DOCTYPE html>
<html lang="nl">
<head>
<meta charset="utf-8">
<title>Praktijk Vorsteling – Visitekaartje</title>
<link rel="stylesheet" href="https://fonts.googleapis.com/css2?family=Montserrat:wght@700&family=Open+Sans:wght@400&family=Roboto:wght@400;500&display=swap">
<style>
  :root {
    --backdrop: #2a2a2b;
    --card: #262627;
    --silver: #a9a9ab;
    --white: #f2f2f2;
    --text-soft: #d6d6d6;
    --accent: #2e8fd1;
    --divider: #8a8a8a;
  }
  * { box-sizing: border-box; margin: 0; padding: 0; }
  html, body {
    width: 1200px; height: 1000px; overflow: hidden;
    background: var(--backdrop);
  }
  .stage {
    position: relative; width: 1200px; height: 1000px;
  }
  .card {
    position: absolute; left: 280px;
    width: 640px; height: 366px;
    background: var(--card);
    box-shadow: 0 10px 30px rgba(0,0,0,.45);
  }
  .card--front { top: 104px; }
  .card--back { top: 530px; }

  .brand {
    position: absolute; inset: 0;
    display: flex; flex-direction: column; align-items: center; justify-content: center;
    gap: 18px;
  }
  .brand__dot {
    width: 84px; height: 84px; border-radius: 50%;
    background: var(--silver);
  }
  .brand__name {
    font-family: "Montserrat", sans-serif; font-weight: 700;
    font-size: 21px; letter-spacing: 0.5px; color: var(--silver);
  }

  .identity {
    position: absolute; right: 342px; top: 122px;
    text-align: right;
  }
  .identity__name {
    font-family: "Roboto", sans-serif; font-weight: 500;
    font-size: 19px; color: var(--white); text-transform: uppercase;
    letter-spacing: -0.2px;
  }
  .identity__role {
    font-family: "Roboto", sans-serif; font-weight: 400;
    font-size: 15px; color: var(--accent); margin-top: 4px;
  }
  .divider {
    position: absolute; left: 318px; top: 122px;
    width: 2px; height: 62px; background: var(--divider);
  }
  .contacts {
    position: absolute; left: 338px; top: 118px;
    list-style: none;
    font-family: "Open Sans", sans-serif; font-size: 16px; color: var(--text-soft);
  }
  .contacts li {
    display: flex; align-items: center; gap: 16px; height: 24px;
  }
  .contacts svg { width: 13px; height: 13px; fill: var(--accent); flex: none; }
  .contacts .highlight { color: var(--accent); }
  .address {
    position: absolute; left: 150px; top: 262px;
    display: flex; align-items: center; gap: 18px;
    font-family: "Open Sans", sans-serif; font-size: 17px; color: var(--text-soft);
    letter-spacing: 0.6px;
  }
  .address svg { width: 14px; height: 20px; fill: var(--accent); }
</style>
</head>
<body>
<main class="stage">
  <section class="card card--front" aria-label="Voorkant visitekaartje">
    <div class="brand">
      <span class="brand__dot"></span>
      <span class="brand__name">PRAKTIJK VORSTELING</span>
    </div>
  </section>

  <section class="card card--back" aria-label="Achterkant visitekaartje">
    <div class="identity">
      <p class="identity__name">Dr. Ilse Vorsteling-ter Haaf</p>
      <p class="identity__role">Psychiater/Kinder- en Jeugdpsychiater</p>
    </div>
    <span class="divider"></span>
    <ul class="contacts">
      <li>
        <svg viewBox="0 0 24 24" aria-hidden="true"><path d="M6.6 10.8a15.1 15.1 0 0 0 6.6 6.6l2.2-2.2a1 1 0 0 1 1-.25 11.4 11.4 0 0 0 3.6.57 1 1 0 0 1 1 1V20a1 1 0 0 1-1 1A17 17 0 0 1 3 4a1 1 0 0 1 1-1h3.5a1 1 0 0 1 1 1c0 1.25.2 2.45.57 3.6a1 1 0 0 1-.25 1z"/></svg>
        <span>06-58190274</span>
      </li>
      <li>
        <svg viewBox="0 0 24 24" aria-hidden="true"><path d="M2 5h20v14H2z M2 5l10 8 10-8" /></svg>
        <span>info@praktijkvorsteling.nl</span>
      </li>
      <li>
        <svg viewBox="0 0 24 24" aria-hidden="true"><circle cx="12" cy="12" r="10"/></svg>
        <span>www.<span class="highlight">praktijkvorsteling</span>.nl</span>
      </li>
    </ul>
    <p class="address">
      <svg viewBox="0 0 14 20" aria-hidden="true"><path d="M7 0a7 7 0 0 0-7 7c0 5 7 13 7 13s7-8 7-13a7 7 0 0 0-7-7zm0 9.5A2.5 2.5 0 1 1 7 4.5a2.5 2.5 0 0 1 0 5z"/></svg>
      <span>Jorisvan Heultstraat 14 3071 PW Rotterdam</span>
    </p>
  </section>
</main>
</body>
</html>
```